Business Card Design

New business card design

Target Market(s)

Residential & Commercial Property Managers

Industry/Entity Type

Plumbing Services

Contact Information for Business Card

Name - Rowan Keddle, title - Director, Phone Number - 0431 286 517, email - rowan@tbk-plumbing.com.au, Company ABN - 73 215 904 386,

Font styles to use
Sans Serif

Colors
0054AA
0677BA
7BADD7
CADEEF
E8F1F8

```html
<!DOCTYPE html>
<html lang="en">
<head>
<meta charset="utf-8">
<title>TBK Plumbing Services – Business Card</title>
<link href="https://fonts.googleapis.com/css2?family=Montserrat:wght@400;600&family=Roboto:wght@300;400&display=swap" rel="stylesheet">
<style>
  :root {
    --bg: #2b2b2b;
    --navy: #0054AA;
    --mid-blue: #0677BA;
    --sky: #7BADD7;
    --ice: #CADEEF;
    --paper: #E8F1F8;
    --ink: #1c2733;
    --grey-text: #5f7285;
    --white: #ffffff;
  }
  * { margin: 0; padding: 0; box-sizing: border-box; }
  html, body { width: 1200px; height: 852px; overflow: hidden; background: var(--bg); }
  .canvas { position: relative; width: 1200px; height: 852px; }

  .card {
    position: absolute;
    width: 560px;
    height: 320px;
    border-radius: 26px;
    overflow: hidden;
    box-shadow: 0 10px 24px rgba(0,0,0,.45);
  }

  /* Back of card */
  .card-back { left: 70px; top: 70px; background: var(--mid-blue); }
  .card-back .brand {
    position: absolute; left: 0; right: 0; top: 118px;
    display: flex; align-items: center; justify-content: center; gap: 14px;
    font-family: "Montserrat", sans-serif; font-weight: 600;
    font-size: 44px; letter-spacing: 4px; color: var(--white);
  }
  .brand-dot { width: 16px; height: 16px; border-radius: 50%; background: var(--ice); }
  .card-back .brand-tag {
    position: absolute; left: 0; right: 0; top: 188px; text-align: center;
    font-family: "Roboto", sans-serif; font-weight: 300; font-size: 15px;
    letter-spacing: 8px; color: var(--ice);
  }

  /* Front of card */
  .card-front { left: 570px; top: 462px; background: var(--paper); }
  .front-curve { position: absolute; inset: 0; }
  .front-brand {
    position: absolute; right: 46px; top: 96px; width: 190px;
    font-family: "Montserrat", sans-serif; font-weight: 600; font-size: 40px;
    letter-spacing: 4px; color: var(--white);
    display: flex; align-items: center; justify-content: center; gap: 12px;
  }
  .front-tag {
    position: absolute; right: 46px; top: 160px; width: 190px; text-align: center;
    font-family: "Roboto", sans-serif; font-weight: 300; font-size: 11px;
    letter-spacing: 5px; color: var(--ice);
  }
  .person { position: absolute; left: 40px; top: 56px; font-family: "Montserrat", sans-serif; }
  .person-name { font-size: 22px; font-weight: 600; color: var(--ink); }
  .person-title { font-family: "Roboto", sans-serif; font-size: 13px; color: var(--grey-text); margin-top: 2px; }

  .contact {
    position: absolute; left: 40px; top: 150px;
    font-family: "Roboto", sans-serif; font-size: 13px; color: var(--ink); line-height: 1.35;
  }
  .contact-address { margin-bottom: 8px; }
  .contact-list { list-style: none; }
  .contact-list li { display: flex; align-items: center; gap: 10px; margin-bottom: 3px; }
  .contact-list svg { width: 12px; height: 12px; fill: var(--mid-blue); flex: none; }
  .abn-label { display: inline-block; width: 12px; font-size: 8px; font-weight: 400; color: var(--mid-blue); }
</style>
</head>
<body>
<main class="canvas">

  <section class="card card-back" aria-label="Card back">
    <div class="brand">tbk <span class="brand-dot"></span></div>
    <p class="brand-tag">plumbing services</p>
  </section>

  <section class="card card-front" aria-label="Card front">
    <svg class="front-curve" viewBox="0 0 560 320" preserveAspectRatio="none" aria-hidden="true">
      <path d="M285 0 C250 90 265 230 330 320 L560 320 L560 0 Z" fill="var(--sky)"/>
      <path d="M300 0 C268 95 285 235 350 320 L560 320 L560 0 Z" fill="var(--navy)"/>
    </svg>
    <div class="front-brand">tbk <span class="brand-dot"></span></div>
    <p class="front-tag">plumbing services</p>

    <div class="person">
      <h1 class="person-name">Rowan Keddle</h1>
      <p class="person-title">Director</p>
    </div>

    <div class="contact">
      <p class="contact-address">12 Harbour Rd, Lindfield,<br>NSW 2070</p>
      <ul class="contact-list">
        <li><svg viewBox="0 0 24 24"><path d="M6.6 10.8a15 15 0 0 0 6.6 6.6l2.2-2.2a1 1 0 0 1 1-.25 11.4 11.4 0 0 0 3.6.57 1 1 0 0 1 1 1V20a1 1 0 0 1-1 1A17 17 0 0 1 3 4a1 1 0 0 1 1-1h3.5a1 1 0 0 1 1 1c0 1.25.2 2.45.57 3.57a1 1 0 0 1-.25 1z"/></svg>0431 286 517</li>
        <li><svg viewBox="0 0 24 24"><path d="M2 5h20v14H2z M2 5l10 8 10-8" fill="none" stroke="var(--mid-blue)" stroke-width="2.4"/></svg>rowan@tbk-plumbing.com.au</li>
        <li><svg viewBox="0 0 24 24"><circle cx="12" cy="12" r="9" fill="none" stroke="var(--mid-blue)" stroke-width="2.2"/><path d="M3 12h18M12 3c3 3 3 15 0 18M12 3c-3 3-3 15 0 18" fill="none" stroke="var(--mid-blue)" stroke-width="1.8"/></svg>www.tbk-plumbing.com.au</li>
        <li><svg viewBox="0 0 24 24"><rect x="3" y="5" width="18" height="14" rx="2" fill="none" stroke="var(--mid-blue)" stroke-width="2.2"/><path d="M7 10h10M7 14h6" stroke="var(--mid-blue)" stroke-width="2"/></svg>ABN 73 215 904 386</li>
      </ul>
    </div>
  </section>

</main>
</body>
</html>
```